Card design for orthopaedic surgeons working as The Brightwater Joint Centre

Business cards, letterhead

Colors

Designer to choose colors to be used in the design.

Requirements
Must have
• Late addition.
• Cards letterhead must have logos of
• Crestmoor Lindell College of Surgeons
• Varenwood Bone Health Association
Nice to have
• Back of card to have space for appointment time to be added by hand and some blank space for writing incidental other notes.

```html
<!DOCTYPE html>
<html lang="en">
<head>
<meta charset="utf-8">
<title>The Brightwater Joint Centre – Business Card</title>
<link rel="stylesheet" href="https://fonts.googleapis.com/css2?family=Montserrat:wght@400;600&display=swap">
<style>
  :root {
    --navy: #0c2f49;
    --sky: #5297cc;
    --paper: #f6f7f8;
    --stage: #e6e8eb;
    --ink-light: #e9eef3;
    --badge: #1d4566;
  }
  * { margin: 0; padding: 0; box-sizing: border-box; }
  html, body { width: 1200px; height: 1021px; overflow: hidden; }
  body {
    background: var(--stage);
    font-family: "Montserrat", sans-serif;
    position: relative;
  }
  .card {
    position: absolute;
    left: 290px;
    width: 620px;
    height: 354px;
    overflow: hidden;
    box-shadow: 0 6px 18px rgba(0,0,0,0.18);
  }
  .card-back { top: 90px; background: var(--navy); }
  .card-front { top: 548px; background: var(--paper); }

  .brand-name {
    font-family: "Montserrat", sans-serif;
    font-weight: 400;
    letter-spacing: -0.2px;
    white-space: nowrap;
  }
  .card-back .brand-name {
    position: absolute; top: 148px; left: 0; width: 100%;
    text-align: center; font-size: 30px; color: var(--ink-light);
  }
  .card-back .web {
    position: absolute; top: 246px; left: 0; width: 100%;
    text-align: center; font-size: 13px; letter-spacing: 0.6px; color: var(--ink-light);
  }
  .affiliations {
    position: absolute; bottom: 22px; right: 24px;
    display: flex; gap: 10px;
  }
  .affiliation-badge {
    width: 30px; height: 30px; border-radius: 50%;
    background: var(--badge);
  }

  .card-front .brand-name {
    position: absolute; top: 50px; left: 40px;
    font-size: 28px; color: var(--navy);
  }
  .holder { position: absolute; top: 118px; left: 40px; }
  .holder-name { font-weight: 600; font-size: 21px; color: var(--sky); }
  .holder-role { font-size: 15px; color: var(--navy); margin-top: 1px; }

  .wave { position: absolute; inset: 0; width: 620px; height: 354px; }

  .contact {
    position: absolute; right: 26px; top: 246px;
    color: var(--ink-light); font-size: 13.5px; line-height: 19px;
    text-align: right;
  }
  .contact .address { margin-bottom: 4px; }
  .contact-line { display: flex; justify-content: flex-end; align-items: center; gap: 8px; white-space: nowrap; }
  .contact-line svg { width: 14px; height: 14px; flex: none; }
  .contact-line .spacer { width: 14px; }
</style>
</head>
<body>

  <section class="card card-back">
    <div class="brand-name">The Brightwater Joint Centre</div>
    <div class="web">www.brightwaterjoint.com</div>
    <div class="affiliations">
      <div class="affiliation-badge" role="img" aria-label="Crestmoor Lindell College of Surgeons badge"></div>
      <div class="affiliation-badge" role="img" aria-label="Varenwood Bone Health Association badge"></div>
    </div>
  </section>

  <section class="card card-front">
    <svg class="wave" viewBox="0 0 620 354" aria-hidden="true">
      <path d="M0,188 C150,220 300,220 420,213 C520,207 580,185 620,150 L620,354 L0,354 Z" fill="#5297cc"/>
      <path d="M0,207 C150,240 300,240 420,233 C520,227 580,205 620,170 L620,354 L0,354 Z" fill="#ffffff"/>
      <path d="M0,210 C150,243 300,243 420,236 C520,230 580,208 620,173 L620,354 L0,354 Z" fill="#0c2f49"/>
    </svg>

    <div class="brand-name">The Brightwater Joint Centre</div>

    <div class="holder">
      <div class="holder-name">Daniel Harper</div>
      <div class="holder-role">Managing Director</div>
    </div>

    <div class="contact">
      <div class="address">
        <div class="contact-line">48 Harbour Lane<span class="spacer"></span></div>
        <div class="contact-line">Eastfield, Avonshire, 20417<span class="spacer"></span></div>
      </div>
      <div class="contact-line">(555) 014-2287
        <svg viewBox="0 0 16 16" aria-hidden="true"><path d="M4 1.5l2.2 3-1.3 1.6c.8 1.8 2.2 3.2 4 4l1.6-1.3 3 2.2-1.2 2.5C7 13.3 2.7 9 2.5 3.7z" fill="#5297cc"/></svg>
      </div>
      <div class="contact-line">daniel@brightwaterjoint.com
        <svg viewBox="0 0 16 16" aria-hidden="true"><rect x="1.5" y="3.5" width="13" height="9" fill="none" stroke="#5297cc" stroke-width="1.4"/><path d="M1.5 3.5L8 9l6.5-5.5" fill="none" stroke="#5297cc" stroke-width="1.4"/></svg>
      </div>
      <div class="contact-line">www.brightwaterjoint.com
        <svg viewBox="0 0 16 16" aria-hidden="true"><g fill="none" stroke="#5297cc" stroke-width="1.2"><circle cx="8" cy="8" r="6.3"/><ellipse cx="8" cy="8" rx="2.8" ry="6.3"/><path d="M1.7 8h12.6M2.7 4.8h10.6M2.7 11.2h10.6"/></g></svg>
      </div>
    </div>
  </section>

</body>
</html>
```